business card deign

Logo needs the following on it.
1. attached logo
2. Tagline - "If it keeps a drink cold or the party going...we do it!"
3. Name- Dalton Pikes, Founder and CPO
4. Address - 412 E. Carver Avenue, Ste 2207, Tampa, FL. 33917
5. Phone - 555.318.4726

```html
<!DOCTYPE html>
<html lang="en">
<head>
<meta charset="utf-8">
<title>CHILVO business card</title>
<link rel="stylesheet" href="https://fonts.googleapis.com/css2?family=Roboto:wght@400;500;700&display=swap">
<style>
  :root {
    --stage: #222222;
    --paper: #ffffff;
    --ink: #111111;
    --ink-soft: #2a2a2a;
    --rule: #1a1a1a;
  }
  * { box-sizing: border-box; margin: 0; padding: 0; }
  html, body {
    width: 1200px; height: 780px; overflow: hidden;
    background: var(--stage);
    font-family: "Roboto", Arial, sans-serif;
    color: var(--ink);
  }
  .canvas {
    position: relative; width: 1200px; height: 780px;
    display: flex; align-items: center; justify-content: center; gap: 40px;
  }
  .card {
    position: relative; width: 540px; height: 310px;
    background: var(--paper); border-radius: 22px; overflow: hidden;
  }
  .brand {
    display: flex; align-items: center; gap: 12px;
    font-weight: 700; letter-spacing: 0.55em; text-transform: uppercase;
    color: var(--ink);
  }
  .brand-mark { width: 14px; height: 14px; background: var(--ink); flex: none; }
  .card-front .brand {
    position: absolute; right: 26px; bottom: 34px; font-size: 24px;
  }
  .card-back .brand {
    position: absolute; right: 26px; top: 78px; font-size: 22px;
  }
  .divider {
    position: absolute; left: 110px; right: 40px; top: 140px;
    height: 1.5px; background: var(--rule);
  }
  .contact {
    position: absolute; right: 36px; top: 160px;
    list-style: none; text-align: right;
    font-size: 13px; line-height: 1.45; color: var(--ink-soft);
  }
  .contact li { display: flex; justify-content: flex-end; align-items: flex-start; gap: 8px; }
  .contact svg { width: 13px; height: 13px; margin-top: 2px; flex: none; }
  .contact .indent { padding-right: 21px; }
  .person {
    position: absolute; left: 0; top: 168px;
    padding-left: 36px; border-left: 22px solid var(--ink);
  }
  .person-name { font-size: 28px; font-weight: 700; line-height: 1.1; }
  .person-role { font-size: 16px; font-weight: 400; color: var(--ink-soft); margin-top: 2px; }
  .person-rule {
    position: absolute; left: 58px; top: 232px; width: 170px;
    height: 1.5px; background: var(--rule);
  }
  .tagline {
    position: absolute; left: 58px; bottom: 30px;
    font-size: 14px; font-weight: 500; line-height: 1.4; color: var(--ink-soft);
  }
</style>
</head>
<body>
<main class="canvas">
  <section class="card card-front" aria-label="Card front">
    <div class="brand"><span class="brand-mark"></span><span>CHILVO</span></div>
  </section>

  <section class="card card-back" aria-label="Card back">
    <div class="brand"><span class="brand-mark"></span><span>CHILVO</span></div>
    <div class="divider"></div>

    <ul class="contact">
      <li>555.318.4726
        <svg viewBox="0 0 24 24" aria-hidden="true"><path fill="#111" d="M6.6 10.8a15 15 0 0 0 6.6 6.6l2.2-2.2c.3-.3.7-.4 1-.2 1.1.4 2.3.6 3.6.6.6 0 1 .4 1 1V20c0 .6-.4 1-1 1A17 17 0 0 1 3 4c0-.6.4-1 1-1h3.5c.6 0 1 .4 1 1 0 1.3.2 2.5.6 3.6.1.3 0 .7-.2 1z"/></svg>
      </li>
      <li>412 E. Carver Avenue,
        <svg viewBox="0 0 24 24" aria-hidden="true"><path fill="#111" d="M12 2a7 7 0 0 0-7 7c0 5 7 13 7 13s7-8 7-13a7 7 0 0 0-7-7zm0 9.5A2.5 2.5 0 1 1 12 6.5a2.5 2.5 0 0 1 0 5z"/></svg>
      </li>
      <li class="indent">Ste 2207, Tampa, FL. 33917</li>
    </ul>

    <div class="person">
      <h1 class="person-name">Dalton Pikes</h1>
      <p class="person-role">Founder and CPO</p>
    </div>
    <div class="person-rule"></div>

    <p class="tagline">If it keeps a drink cold or<br>the party going...we do it!</p>
  </section>
</main>
</body>
</html>
```